** Wanted ** Wordpress web design for scaffolding rental and construction company

We need a website design and must be functional to show a basic overview of what our company offers as a service. We have a domain name and a logo but we need web design. This web site should have another scaffolding rental page for construction and renovation as well as a quote section where customers can enter their personal information and also upload photos. The site% 26quot; www.brindlework.com% 26quot; should be intuitive, clear and classy ... The logo must be found on the site in several ways.

Target Market(s)

Professional and no professional

Coding

Coded - Design and coding required

Number of Pages Required

3 page

Font styles to use
Serif
Sans Serif
Decorative
Script

Requirements
Must have
• Our logo
Nice to have
• Slogan:% 26quot; The height% 26 # 224; port% 26 # 233; e hand% 26quot;

```html
<!DOCTYPE html>
<html lang="en">
<head>
<meta charset="utf-8">
<title>Brindlework – Scaffolding &amp; Construction</title>
<link href="https://fonts.googleapis.com/css2?family=Lato:wght@400;700;900&family=Kanit:wght@500;600&display=swap" rel="stylesheet">
<style>
:root{
  --orange:#f7821b;
  --dark:#2b2d31;
  --darker:#232427;
  --ink:#1d1d1d;
  --grey-text:#7a7a7a;
  --light:#f2f2f2;
  --line:#e3e3e3;
  --white:#fff;
}
*{box-sizing:border-box;margin:0;padding:0}
html,body{width:1200px;height:4003px;overflow:hidden}
body{position:relative;font-family:'Lato',sans-serif;color:var(--ink);background:var(--white)}
.abs{position:absolute}
p{font-size:11px;line-height:20px;color:var(--grey-text)}
.btn{position:absolute;background:var(--orange);color:#fff;font-weight:700;border-radius:4px;display:flex;align-items:center;justify-content:center}
.section-title{position:absolute;font-family:'Kanit',sans-serif;font-weight:500;font-size:26px;color:var(--ink)}
.rule{position:absolute;height:1px;background:var(--line)}

/* top bar & header */
.topbar{left:0;top:0;width:1200px;height:59px;background:var(--light)}
.topbar span{position:absolute;top:22px;font-size:11px;color:#333}
.header{left:0;top:59px;width:1200px;height:91px;background:#fff}
.logo-panel{left:0;top:30px;width:420px;height:150px;background:#fff;clip-path:polygon(0 0,390px 0,420px 29px,420px 89px,390px 150px,0 150px)}
.brand{position:absolute;display:flex;align-items:center;gap:10px;font-family:'Kanit',sans-serif;font-weight:600;color:var(--orange);letter-spacing:1px}
.brand i{display:block;background:var(--orange)}
.nav{left:480px;top:98px;display:flex;gap:32px;font-size:11px;color:#555}
.icon-box{position:absolute;width:36px;height:36px;border-radius:4px}

/* hero */
.hero{left:0;top:150px;width:1200px;height:601px;background:linear-gradient(180deg,#3a352d 0%,#4d3e2c 55%,#2c251e 100%)}
.hero-title{left:0;top:345px;width:1200px;text-align:center;font-family:'Kanit',sans-serif;font-weight:600;font-size:62px;color:#fff}
.hero-text{left:350px;top:430px;width:500px;text-align:center;font-size:12.5px;line-height:22px;color:#eee}
.dot{position:absolute;width:9px;height:9px;border:1.5px solid #fff;transform:rotate(45deg)}

/* services */
.card{position:absolute;width:280px;height:323px;background:#fff;box-shadow:0 0 8px rgba(0,0,0,.12)}
.card .ph{position:absolute;left:8px;top:8px;width:264px;height:150px}
.card h3{position:absolute;left:16px;top:178px;font-weight:400;font-size:16px}
.card p{position:absolute;left:16px;top:200px;width:250px;font-size:10.5px}
.card a{position:absolute;left:22px;top:273px;font-size:11px;color:var(--orange);text-decoration:none;border-bottom:1px solid var(--orange)}
.msg{left:760px;top:827px;width:278px;height:404px;border:1px solid var(--line)}
.field{position:absolute;left:20px;width:240px;height:40px;border:1px solid #ccc;border-radius:4px;background:#f2f2f2;font-size:10px;color:#777;padding:13px 16px}

/* projects */
.projects{left:0;top:1321px;width:1200px;height:688px;background:var(--light);clip-path:polygon(60px 0,1140px 0,1200px 70px,1200px 618px,1140px 688px,60px 688px,0 618px,0 70px)}
.tabs{left:165px;top:1428px;display:flex;gap:34px;font-size:11.5px;color:#444}
.tile{position:absolute;width:210px;height:210px;border-radius:6px}

/* testimonials */
.testi{left:0;top:2486px;width:1200px;height:414px;background:linear-gradient(180deg,#2e3035,#24262a);clip-path:polygon(60px 0,1140px 0,1200px 70px,1200px 344px,1140px 414px,60px 414px,0 344px,0 70px)}
.quote{position:absolute;width:278px;height:90px;background:#fff;padding:14px 16px;font-size:10px;line-height:20px;color:#777}
.quote:after{content:"";position:absolute;left:60px;bottom:-12px;border:7px solid transparent;border-top:6px solid #fff;border-left:6px solid #fff}
.client{position:absolute;display:flex;gap:14px;align-items:center}
.client .av{width:52px;height:52px;background:linear-gradient(#9aa0a8,#5a6068)}
.client b{display:block;font-size:12.5px;color:#fff}
.client small{font-size:10.5px;color:var(--orange)}

/* contact & footer */
.contact{left:0;top:3375px;width:1200px;height:264px;background:var(--light)}
.footer{left:0;top:3608px;width:1200px;height:395px;background:var(--dark);clip-path:polygon(0 31px,410px 31px,440px 0,1200px 0,1200px 395px,0 395px)}
.footer h4{position:absolute;font-weight:700;font-size:14px;color:#fff}
.footer ul{position:absolute;list-style:none;font-size:10.5px;color:#ccc;line-height:19.5px}
.footer li:before{content:"+";color:#999;margin-right:10px}
.social{position:absolute;width:36px;height:36px;border:1px solid #777}
.copyright{left:0;top:3970px;width:1200px;height:33px;background:var(--darker);color:#ccc;font-size:10.5px;text-align:center;line-height:33px}
</style>
</head>
<body>

<!-- top bar -->
<div class="abs topbar">
  <svg class="abs" style="left:428px;top:20px" width="18" height="18" viewBox="0 0 24 24"><path fill="#f7821b" d="M6.6 10.8a15 15 0 0 0 6.6 6.6l2.2-2.2c.3-.3.7-.4 1-.2 1.1.4 2.3.6 3.6.6.6 0 1 .4 1 1V20c0 .6-.4 1-1 1A17 17 0 0 1 3 4c0-.6.4-1 1-1h3.5c.6 0 1 .4 1 1 0 1.3.2 2.5.6 3.6.1.3 0 .7-.2 1z"/></svg>
  <span style="left:462px">+91-000-000-0000</span>
  <svg class="abs" style="left:626px;top:22px" width="18" height="13" viewBox="0 0 18 13"><rect width="18" height="13" fill="#f7821b"/><path d="M0 0l9 7 9-7" stroke="#fff" fill="none"/></svg>
  <span style="left:658px">support@brindlework.com</span>
  <svg class="abs" style="left:906px;top:23px" width="130" height="12"><circle cx="6" cy="6" r="4" fill="#999"/><circle cx="44" cy="6" r="4" fill="#999"/><circle cx="84" cy="6" r="4" fill="#999"/><circle cx="124" cy="6" r="4" fill="#999"/></svg>
</div>
<div class="abs header"></div>
<div class="abs logo-panel"></div>
<div class="brand" style="left:162px;top:120px;font-size:24px"><i style="width:22px;height:22px"></i>BRINDLEWORK</div>
<div class="abs nav"><span>Home</span><span>About Us</span><span>Services</span><span>Testimonials</span><span>Gallery</span><span>Contact Us</span></div>
<div class="icon-box" style="left:956px;top:87px;background:#e4e4e4">
  <svg width="36" height="36"><circle cx="17" cy="17" r="5" fill="none" stroke="#666" stroke-width="1.5"/><path d="M21 21l4 4" stroke="#666" stroke-width="1.5"/></svg>
</div>
<div class="icon-box" style="left:1001px;top:87px;background:var(--orange)">
  <svg width="36" height="36"><circle cx="18" cy="14" r="4" fill="#fff"/><path d="M11 26a7 7 0 0 1 14 0z" fill="#fff"/></svg>
</div>

<!-- hero -->
<div class="abs hero" role="img" aria-label="Timber-framed house under construction at dusk"></div>
<h1 class="abs hero-title">The Height, Port</h1>
<p class="abs hero-text">Lorem Ipsum is simply dummy text of the printing and typesetting industry. Lorem Ipsum has been the industry's standard dummy text ever since the 1500s</p>
<div class="btn" style="left:499px;top:510px;width:201px;height:51px;font-size:17px">Request A Quote</div>
<div class="dot" style="left:532px;top:688px"></div>
<div class="dot" style="left:576px;top:688px"></div>
<div class="dot" style="left:618px;top:688px;background:#fff"></div>
<div class="dot" style="left:659px;top:688px"></div>

<!-- services -->
<h2 class="section-title" style="left:163px;top:824px">Our Services</h2>
<div class="rule" style="left:348px;top:842px;width:272px"></div>
<div class="icon-box" style="left:652px;top:827px;width:30px;height:30px;background:#eee;text-align:center;line-height:30px;color:#888;font-size:12px">‹</div>
<div class="icon-box" style="left:690px;top:827px;width:30px;height:30px;background:#eee;text-align:center;line-height:30px;color:#888;font-size:12px">›</div>

<div class="card" style="left:160px;top:909px">
  <div class="ph" role="img" aria-label="Scaffolding frame against a pink evening sky" style="background:linear-gradient(180deg,#8f93b8,#d6a6b2)"></div>
  <h3>Scaffolding</h3>
  <p>Lorem Ipsum is simply dummy text of the printing and typesetting industry. Lorem Ipsum has been the industry's standard dummy text.</p>
  <a>Read More</a>
</div>
<div class="card" style="left:460px;top:909px">
  <div class="ph" role="img" aria-label="Lift shaft inside a modern building" style="background:linear-gradient(180deg,#2a4f5c,#4e8196,#1d3a45)"></div>
  <h3>Elevation</h3>
  <p>Lorem Ipsum is simply dummy text of the printing and typesetting industry. Lorem Ipsum has been the industry's standard dummy text.</p>
  <a>Read More</a>
</div>

<div class="abs msg">
  <h3 class="abs" style="left:20px;top:28px;font-size:17px;font-weight:700">Drop A Message</h3>
  <div class="rule" style="left:180px;top:40px;width:78px"></div>
  <p class="abs" style="left:20px;top:62px;width:245px;font-size:10.5px">Lorem Ipsum is simply dummy text of the printing and typesetting industry.</p>
  <div class="field" style="top:124px">Your Name:</div>
  <div class="field" style="top:176px">Your Email:</div>
  <div class="field" style="top:228px;height:76px">Message:</div>
  <div class="btn" style="left:20px;top:323px;width:150px;height:36px;font-size:14px">Send A Message</div>
</div>

<!-- projects -->
<div class="abs projects"></div>
<h2 class="section-title" style="left:163px;top:1378px">Our Projects</h2>
<div class="rule" style="left:352px;top:1396px;width:686px"></div>
<div class="abs tabs"><span style="border-bottom:2px solid var(--orange);padding-bottom:4px">All Projects</span><span>Scaffolding</span><span>Renovation</span><span>Elevation</span></div>

<div class="tile" style="left:160px;top:1497px;background:linear-gradient(#9ab7c9,#5f7a4f)" role="img" aria-label="Timber frame building with a crane"></div>
<div class="tile" style="left:383px;top:1497px;background:#1f2226;color:#fff;text-align:center;padding:60px 18px 0">
  <div style="font-size:15px;font-weight:700;margin-bottom:8px">Elevation</div>
  <div style="font-size:10.5px;line-height:19.5px;color:#eee">Lorem Ipsum is simply dummy text of the printing and typesetting industry. Lorem Ipsum has been the industry's standard dummy text.</div>
</div>
<div class="tile" style="left:606px;top:1497px;background:linear-gradient(90deg,#c9dbe8,#4f6f8c)" role="img" aria-label="Glass skyscraper facade"></div>
<div class="tile" style="left:828px;top:1497px;background:linear-gradient(#dde4ea,#5f6368)" role="img" aria-label="Towers and cranes on a skyline"></div>
<div class="tile" style="left:160px;top:1719px;background:linear-gradient(#7fb3dc,#8c7558)" role="img" aria-label="Curved building frame under construction"></div>
<div class="tile" style="left:383px;top:1719px;background:linear-gradient(#d9dee3,#555a60)" role="img" aria-label="High-rise apartment block"></div>
<div class="tile" style="left:606px;top:1719px;background:linear-gradient(#8a6a4c,#4f5a3c)" role="img" aria-label="Workers on scaffolding"></div>
<div class="tile" style="left:828px;top:1719px;background:linear-gradient(#9cb8d4,#b08659,#7a4b31)" role="img" aria-label="Timber house with sheathed roof"></div>

<!-- about -->
<div class="tile" style="left:207px;top:2070px;width:337px;height:339px;border-radius:12px;background:linear-gradient(135deg,#b8b2a8,#5d7db8)" role="img" aria-label="Two engineers in hard hats reviewing plans"></div>
<h2 class="section-title" style="left:613px;top:2088px">About Us</h2>
<div class="rule" style="left:750px;top:2106px;width:288px"></div>
<p class="abs" style="left:612px;top:2134px;width:330px;font-size:10.5px">Lorem Ipsum is simply dummy text of the printing and typesetting industry. Lorem Ipsum has been the industry's standard dummy text ever since the 1500s, when an unknown printer took a galley of type and scrambled it to make a type specimen book. It has survived not only five centuries, but also the leap into electronic typesetting, remaining essentially unchanged.</p>
<p class="abs" style="left:612px;top:2272px;width:330px;font-size:10.5px">It was popularised in the 1960s with the release of Letraset sheets containing Lorem Ipsum passages.</p>
<div class="btn" style="left:612px;top:2350px;width:119px;height:36px;font-size:14px">Read More</div>

<!-- testimonials -->
<div class="abs testi" role="img" aria-label="Dark cityscape behind the testimonials"></div>
<div class="rule" style="left:160px;top:2557px;width:315px;background:#666"></div>
<div class="rule" style="left:725px;top:2557px;width:313px;background:#666"></div>
<h2 class="section-title" style="left:0;top:2539px;width:1200px;text-align:center;color:#fff">Our Testimonials</h2>

<div class="quote" style="left:160px;top:2622px">" Lorem Ipsum is simply dummy text of the printing and typesetting industry. Lorem Ipsum has been the industry's standard dummy text. "</div>
<div class="quote" style="left:460px;top:2622px">" Lorem Ipsum is simply dummy text of the printing and typesetting industry. Lorem Ipsum has been the industry's standard dummy text. "</div>
<div class="quote" style="left:760px;top:2622px">" Lorem Ipsum is simply dummy text of the printing and typesetting industry. Lorem Ipsum has been the industry's standard dummy text. "</div>
<div class="client" style="left:172px;top:2732px"><div class="av" role="img" aria-label="Client portrait"></div><div><b>-Client Name</b><small>Renovation worker</small></div></div>
<div class="client" style="left:472px;top:2732px"><div class="av" role="img" aria-label="Client portrait"></div><div><b>-Client Name</b><small>Renovation worker</small></div></div>
<div class="client" style="left:772px;top:2732px"><div class="av" role="img" aria-label="Client portrait"></div><div><b>-Client Name</b><small>Renovation worker</small></div></div>
<div class="abs" style="left:558px;top:2828px;width:8px;height:8px;background:#fff"></div>
<div class="abs" style="left:596px;top:2828px;width:8px;height:8px;background:var(--orange)"></div>
<div class="abs" style="left:634px;top:2828px;width:8px;height:8px;background:#fff"></div>

<!-- why us -->
<h2 class="section-title" style="left:163px;top:2982px">Why Us?</h2>
<div class="rule" style="left:315px;top:3000px;width:275px"></div>
<p class="abs" style="left:163px;top:3028px;width:330px;font-size:10.5px">Lorem Ipsum is simply dummy text of the printing and typesetting industry. Lorem Ipsum has been the industry's standard dummy text ever since the 1500s, when an unknown printer took a galley of type and scrambled it to make a type specimen book. It has survived not only five centuries, but also the leap into electronic typesetting, remaining essentially unchanged.</p>
<p class="abs" style="left:163px;top:3166px;width:330px;font-size:10.5px">It was popularised in the 1960s with the release of Letraset sheets containing Lorem Ipsum passages.</p>
<div class="btn" style="left:162px;top:3242px;width:119px;height:36px;font-size:14px">Read More</div>
<div class="tile" style="left:656px;top:2963px;width:337px;height:338px;border-radius:12px;background:linear-gradient(160deg,#4d9cb8,#3a5f6a,#6b4a3a)" role="img" aria-label="Tower block rising in scaffolding"></div>

<!-- contact -->
<div class="abs contact"></div>
<h2 class="section-title" style="left:0;top:3421px;width:1200px;text-align:center">Contact Us</h2>
<p class="abs" style="left:365px;top:3460px;width:470px;text-align:center;font-size:10.5px">Lorem Ipsum is simply dummy text of the printing and typesetting industry. Lorem Ipsum has been the industry's standard dummy text ever since the 1500s, when an unknown printer took a galley of type and scrambled it to make a type specimen book.</p>
<div class="icon-box" style="left:492px;top:3541px;width:44px;height:44px;background:var(--orange)">
  <svg width="44" height="44" viewBox="-10 -10 44 44"><path fill="#fff" d="M6.6 10.8a15 15 0 0 0 6.6 6.6l2.2-2.2c.3-.3.7-.4 1-.2 1.1.4 2.3.6 3.6.6.6 0 1 .4 1 1V20c0 .6-.4 1-1 1A17 17 0 0 1 3 4c0-.6.4-1 1-1h3.5c.6 0 1 .4 1 1 0 1.3.2 2.5.6 3.6.1.3 0 .7-.2 1z"/></svg>
</div>
<div class="abs" style="left:551px;top:3552px;font-size:19px;color:var(--orange)">+91-000-000-0000</div>

<!-- footer -->
<div class="abs footer">
  <div class="brand" style="left:162px;top:105px;font-size:19px"><i style="width:18px;height:18px"></i>BRINDLEWORK</div>
  <p class="abs" style="left:163px;top:150px;width:190px;font-size:10.5px;color:#ccc">Lorem Ipsum is simply dummy text of the printing and typesetting industry. Lorem Ipsum has been the industry's standard dummy text ever since the 1500s, when an unknown printer took a galley of type.</p>
  <h4 style="left:388px;top:103px">Usefull Link</h4>
  <ul style="left:386px;top:149px"><li>Home</li><li>About Us</li><li>Services</li><li>Gallery</li><li>Testimonials</li><li>Contact Us</li></ul>
  <h4 style="left:612px;top:103px">Services</h4>
  <ul style="left:610px;top:149px"><li>Scaffolding</li><li>Elevation</li><li>Renovation</li></ul>
  <h4 style="left:838px;top:103px">Usefull Link</h4>
  <div class="abs" style="left:836px;top:149px;font-size:10.5px;color:#ccc;line-height:20px">
    <div style="margin-left:32px">+91-000-000-0000</div>
    <div style="margin-left:32px;margin-top:25px">support@brindlework.com</div>
    <div style="margin-left:32px;margin-top:25px;width:140px">100 lorem ipsum is simply dummy text.</div>
  </div>
  <svg class="abs" style="left:836px;top:150px" width="20" height="110">
    <path fill="#f7821b" transform="scale(.75)" d="M6.6 10.8a15 15 0 0 0 6.6 6.6l2.2-2.2c.3-.3.7-.4 1-.2 1.1.4 2.3.6 3.6.6.6 0 1 .4 1 1V20c0 .6-.4 1-1 1A17 17 0 0 1 3 4c0-.6.4-1 1-1h3.5c.6 0 1 .4 1 1 0 1.3.2 2.5.6 3.6.1.3 0 .7-.2 1z"/>
    <rect x="0" y="49" width="18" height="13" fill="#f7821b"/><path d="M0 49l9 7 9-7" stroke="#2b2d31" fill="none"/>
    <path d="M9 90c-4 0-7 3-7 7 0 5 7 12 7 12s7-7 7-12c0-4-3-7-7-7z" fill="#f7821b"/><circle cx="9" cy="97" r="2.5" fill="#2b2d31"/>
  </svg>
  <div class="social" style="left:514px;top:268px"></div>
  <div class="social" style="left:558px;top:268px"></div>
  <div class="social" style="left:604px;top:268px"></div>
  <div class="social" style="left:648px;top:268px"></div>
</div>
<div class="abs copyright">Copyright © 2020 Brindlework. All Rights Reserved. Terms &amp; Conditions | Privacy Policy</div>

</body>
</html>
```